Tarlow Plumbing & Heating Limited needs a service and maintenance contract document design

Tarlow Plumbing & Heating Limited are a well established family owned and operated company.

We currently offer installation, service and repair services for gas, plumbing, heating and electrical work. We wish to offer service and maintenance plans for plumbing, heating and electrical for our domestic clients in the UK. We would like the brochure to incorporate our company logo and colours, and reflect the reliable, quality, 5 star service we offer our clients.
I have attached a brochure that a friends company uses to give a good idea of the structure of the plans we wish to offer. We want to give our customers a choice in what packages best suit their needs. However, the pricing structure and certain elements/content of what we offer will be slightly different due to our geographical location.

We would like to have the basic structure of the brochure put in place and the
text content editable to our specific needs. Looking for advice on this but we do have Acrobat DC if we need to edit the text ourselves?

We use our logo with "TARLOW" in white over a grey backgound.

Our website is - www.tarlow.plumbing
Facebook and twitter handle is - @TarlowHeating

Target Market(s)

UK domestic plumbing, heating, natural gas, LPG and electrical market. Both private homeowners and landlords. Please see both the domestic and landlord document files attached for an idea on what we'd like.

Colors

Designer to choose colors to be used in the design.

Requirements
Must have
• Would like the finished design to incorporate the branding and colours we already use. Professional, Contemporary designs that will stand out above our competition.
• The content of the brochures MUST be very similar in structure to the files I’ve attached to the brief.
• We are having many designs submitted that are just copying our website content. This is not what we are asking for.
• I would like the icons etc to be redesigned so they are ours and not copied.
• Please also see the Landlords brochure attached to the brief. We would like this to be a separate document but to reflect the same design as the homeowner design you submit.
• The content of the documents will need to be re worded for our own use but I'm happy to change this once the design element is in place.
• A4 sized pages as per the example I've attached
• Must be able to attach the document to our website for clients to download.
Nice to have
• A4 sized pages as per the examples I've attached
Should not have
• Please DO NOT copy the content from our website to create our service plan brochures. This is not what we are after. As above, we need the brochures to be like the ones we've provided but made to fit our brand.
• Thank you

```html
<!DOCTYPE html>
<html lang="en">
<head>
<meta charset="utf-8">
<title>Tarlow Plumbing &amp; Heating – Getting in touch</title>
<link rel="stylesheet" href="https://fonts.googleapis.com/css2?family=Montserrat:wght@300;400;600;700&display=swap">
<style>
  :root {
    --canvas: #ffffff;
    --page-black: #020203;
    --flame-blue: #2f7fd8;
    --flame-deep: #0b2a5c;
    --burner-glow: #3a4a66;
    --text-white: #ffffff;
    --text-soft: #c9ccd3;
  }
  * { margin: 0; padding: 0; box-sizing: border-box; }
  html, body {
    width: 1200px; height: 1200px; overflow: hidden;
    background: var(--canvas);
    font-family: "Montserrat", Arial, sans-serif;
  }
  .page {
    position: absolute; left: 197px; top: 31px;
    width: 806px; height: 1138px;
    background: var(--page-black);
    box-shadow: 4px 4px 10px rgba(0,0,0,0.35);
    overflow: hidden;
    color: var(--text-white);
  }
  .page__photo {
    position: absolute; inset: 0;
    background: linear-gradient(180deg,
      var(--page-black) 0%,
      #0a0a0f 18%,
      var(--flame-deep) 28%,
      var(--flame-blue) 38%,
      var(--flame-deep) 44%,
      var(--burner-glow) 50%,
      #05070c 58%,
      #020203 75%,
      var(--flame-deep) 84%,
      var(--flame-blue) 92%,
      var(--flame-deep) 100%);
  }
  .contact {
    position: absolute; left: 49px; top: 534px; right: 49px;
  }
  .contact__title {
    font-weight: 700; font-size: 45px; line-height: 1; letter-spacing: 0.2px;
  }
  .contact__intro {
    margin-top: 38px;
    font-weight: 300; font-size: 15.5px; line-height: 17px;
  }
  .contact__details {
    margin-top: 23px;
    font-style: normal; font-size: 16px; line-height: 19.5px;
  }
  .contact__details strong { font-weight: 700; }
  .contact__details .light { font-weight: 300; color: var(--text-soft); }
  .contact__details .regular { font-weight: 400; }
  .page__footer {
    position: absolute; left: 49px; top: 1073px;
    font-size: 12px; font-weight: 600;
  }
  .page__footer .page-number { font-weight: 400; margin-right: 6px; }
</style>
</head>
<body>
  <article class="page">
    <div class="page__photo" role="img" aria-label="Close-up photograph of blue gas hob burner flames against a dark background"></div>

    <section class="contact">
      <h1 class="contact__title">Getting in touch</h1>
      <p class="contact__intro">Please contact Martin at info@tarlow.plumbing for an initial discussion or visit our website www.tarlow.plumbing for further information.</p>
      <address class="contact__details">
        <strong>How to contact</strong><br>
        <strong>Tarlow Plumbing &amp; Heating Limited</strong><br>
        <strong>Meridian House</strong><br>
        <span class="light">12 Harrow Lane, Seabrook</span><br>
        <strong>Kent,</strong> <span class="light">CT9 4QX</span><br>
        <strong>01632 960418</strong><br>
        <strong>info@</strong><span class="regular">tarlow.plumbing</span><br>
        <span class="regular">www.tarlow.plumbing</span>
      </address>
    </section>

    <footer class="page__footer"><span class="page-number">12</span>| tarlow.plumbing</footer>
  </article>
</body>
</html>
```